High Tech Real Estate Startup needs a business card

We are developing an innovative real estate marketing product based around advanced search and virtual reality.

We talk to people, we need business cards.

Target Market(s)

The target market is technology professionals and realtors.

Contact Information for Business Card

The information to be included will include

Name
Title
Phone Number
E-mail Address
www.zelquin.com

It should use simple iconography for each one of those fields.

Font styles to use
Other font styles liked:
• Co, Jubilat, Avenir

Colors

Designer to choose colors to be used in the design.

Requirements
Must have
• Clean aesthetic,
• Good use of negative space.
• It should use our company logo, shown in the attached file. It is able to use the negative of that logo (coloured font and white background) and I have attached other acceptable accent colours in a swatch file.
Should not have
• Should not be too busy
• No extraneous text (slogans, tag lines etc)

```html
<!DOCTYPE html>
<html lang="en">
<head>
<meta charset="UTF-8">
<title>Zelquin Business Card</title>
<link href="https://fonts.googleapis.com/css2?family=Montserrat:wght@400;500&family=Open+Sans:wght@400;600&display=swap" rel="stylesheet">
<style>
  :root {
    --page-bg: #2b2b2d;
    --card-bg: #1f1f21;
    --accent: #3fbcbf;
    --text-light: #f2f2f2;
    --icon-glyph: #1f1f21;
  }
  * { margin: 0; padding: 0; box-sizing: border-box; }
  html, body {
    width: 799px;
    height: 1200px;
    overflow: hidden;
    background: var(--page-bg);
  }
  .canvas {
    position: relative;
    width: 799px;
    height: 1200px;
  }
  .card {
    position: absolute;
    left: 80px;
    width: 640px;
    height: 366px;
    background: var(--card-bg);
    border-radius: 26px;
    box-shadow: 0 14px 30px rgba(0,0,0,0.45);
    overflow: hidden;
  }
  .card--front { top: 120px; }
  .card--back { top: 714px; }

  .brand-name {
    font-family: "Montserrat", sans-serif;
    font-weight: 500;
    color: var(--accent);
    letter-spacing: 4px;
    line-height: 1;
  }
  .card--front .brand-name {
    position: absolute;
    left: 0; right: 0;
    top: 150px;
    text-align: center;
    font-size: 62px;
  }
  .card--back .brand-name {
    position: absolute;
    right: 44px;
    top: 70px;
    font-size: 54px;
  }

  .identity {
    position: absolute;
    left: 40px;
    top: 232px;
    display: flex;
    align-items: baseline;
    gap: 14px;
  }
  .identity__name {
    font-family: "Open Sans", sans-serif;
    font-weight: 600;
    font-size: 22px;
    color: var(--text-light);
  }
  .identity__title {
    font-family: "Open Sans", sans-serif;
    font-weight: 600;
    font-size: 13px;
    color: var(--accent);
  }
  .divider {
    position: absolute;
    left: 40px;
    right: 40px;
    top: 272px;
    height: 1px;
    background: var(--accent);
  }
  .contacts {
    position: absolute;
    left: 40px;
    top: 290px;
    display: flex;
    gap: 26px;
    list-style: none;
  }
  .contacts__item {
    display: flex;
    align-items: center;
    gap: 8px;
    font-family: "Open Sans", sans-serif;
    font-size: 14px;
    color: var(--text-light);
  }
  .contacts__icon {
    width: 18px;
    height: 18px;
    flex: none;
  }
</style>
</head>
<body>
<main class="canvas">

  <section class="card card--front" aria-label="Card front">
    <div class="brand-name">ZELQUIN</div>
  </section>

  <section class="card card--back" aria-label="Card back">
    <div class="brand-name">ZELQUIN</div>

    <div class="identity">
      <span class="identity__name">Alex Rowan Hale</span>
      <span class="identity__title">Managing Director</span>
    </div>

    <div class="divider"></div>

    <ul class="contacts">
      <li class="contacts__item">
        <svg class="contacts__icon" viewBox="0 0 18 18" aria-hidden="true">
          <circle cx="9" cy="9" r="9" fill="var(--accent)"/>
          <path d="M6 4.8c.4-.3.9-.2 1.1.2l.9 1.6c.2.4.1.8-.2 1l-.6.5c.5 1 1.3 1.8 2.3 2.3l.5-.6c.2-.3.7-.4 1-.2l1.6.9c.4.2.5.7.2 1.1l-.6.8c-.4.5-1.1.7-1.7.4C8.1 12 6 9.9 5.1 7.5c-.3-.6-.1-1.3.4-1.7z" fill="var(--icon-glyph)"/>
        </svg>
        555.555.5555
      </li>
      <li class="contacts__item">
        <svg class="contacts__icon" viewBox="0 0 18 18" aria-hidden="true">
          <circle cx="9" cy="9" r="9" fill="var(--accent)"/>
          <rect x="4.5" y="6" width="9" height="6.5" rx="0.8" fill="var(--icon-glyph)"/>
          <path d="M4.8 6.4 9 9.6l4.2-3.2" fill="none" stroke="var(--accent)" stroke-width="0.9"/>
        </svg>
        alexhale@zelquin.com
      </li>
      <li class="contacts__item">
        <svg class="contacts__icon" viewBox="0 0 18 18" aria-hidden="true">
          <circle cx="9" cy="9" r="9" fill="var(--accent)"/>
          <g fill="none" stroke="var(--icon-glyph)" stroke-width="1">
            <circle cx="9" cy="9" r="4.6"/>
            <ellipse cx="9" cy="9" rx="2" ry="4.6"/>
            <path d="M4.4 9h9.2M5 6.8h8M5 11.2h8"/>
          </g>
        </svg>
        www.zelquin.com
      </li>
    </ul>
  </section>

</main>
</body>
</html>
```